Keystonery Billboard - Financial Services Company (Investments, Tax Planning and Insurance)

Our new office has a billboard directly above the office building. We'd like something eye-catching with a strong Call to Action, with the main part of the billboard being under 7 words if possible. We'd like you to include a way to get ahold of us (either our website keystoneryllc.example or our phone number 302-418-2907. You may also include in small font something to indicate that we've been serving the area since 1980 (the DE area, the tri-state area, the Marlowe Hollow, etc.)

We offer financial planning, tax planning, and insurance, and we help our clients to focus on their goals and happiness by providing everything they need for lifelong wealth under one roof.

Our logos are attached, we use a triangle logo with green and gray. We use the tagline "discover lasting prosperity" but this does not need to be included.

Potential ideas we have seen from other financial companies-
- the concept that the driver spends more time looking at billboards than planning for their retirement
-something along the lines of "everything you need for your finances is in this building right here" planning, investments, taxes, insurance"
-don't spend your time worrying about retirement, let us help you plan for it
-are you working for your money, or is it working for you?
- retirement takes planning, we're here to help
- ready to retire? talk to us
- need investment advice?
- need help investing?
- crossing your fingers isn't a retirement plan. we can help.
- retiring soon? you need help.

Those are just general ideas, please feel free to be creative.

brand colors:
#00b585
#00b185
#000000
#ffffff
#6d6f75
#6d6f75
#6f7074
#021712
#052e24

```html
<!DOCTYPE html>
<html lang="en">
<head>
<meta charset="utf-8">
<title>Keystonery Billboard</title>
<link rel="stylesheet" href="https://fonts.googleapis.com/css2?family=Montserrat:wght@600;700;800&family=Tinos:wght@700&display=swap">
<style>
  :root {
    --forest: #00402c;
    --forest-deep: #003b28;
    --mid-green: #238a5a;
    --mint: #66f0a0;
    --accent-green: #00a060;
    --url-green: #009462;
    --slate: #6d6f75;
    --white: #ffffff;
    --stage: #e9e9e9;
  }
  * { margin: 0; padding: 0; box-sizing: border-box; }
  html, body {
    width: 1000px; height: 1200px; overflow: hidden;
    background: var(--stage);
  }
  .billboard {
    position: absolute; left: 20px; top: 361px;
    width: 960px; height: 478px;
    background: var(--white);
    font-family: "Montserrat", sans-serif;
    box-shadow: 0 10px 30px rgba(0,0,0,.25);
    overflow: hidden;
  }
  .hero {
    position: absolute; left: 0; top: 10px; width: 960px; height: 322px;
    background: linear-gradient(90deg, var(--forest-deep) 0%, #155f42 30%, var(--mid-green) 55%, #4cc784 75%, var(--mint) 88%);
  }
  .url-corner { position: absolute; left: 0; top: 0; }
  .site-url {
    position: absolute; right: 26px; top: 30px;
    font-size: 24px; font-weight: 700; color: var(--url-green);
    white-space: nowrap;
  }
  .site-url .tld { font-weight: 600; color: var(--slate); }
  .headline {
    position: absolute; left: 46px; top: 34px;
    color: var(--white); font-weight: 800;
    font-size: 70px; line-height: 85px; letter-spacing: -.5px;
    text-transform: uppercase;
  }
  .here-flag { position: absolute; left: 740px; top: 83px; }
  .here-label {
    position: absolute; left: 740px; top: 148px; width: 172px;
    text-align: center; color: var(--white);
    font-size: 44px; font-weight: 800;
  }
  .services {
    position: absolute; left: 0; top: 332px; width: 960px; height: 77px;
    background: linear-gradient(90deg, #e3e3e3, #ffffff 60%, #f6f6f6);
    display: flex; align-items: center; justify-content: center; gap: 18px;
    font-family: "Tinos", serif; font-weight: 700; font-size: 40px;
    color: var(--slate); white-space: nowrap;
  }
  .services .divider { color: var(--accent-green); font-family: "Montserrat", sans-serif; font-weight: 600; font-size: 30px; }
  .contact-bar {
    position: absolute; left: 0; top: 409px; width: 960px; height: 69px;
    background: var(--forest-deep);
    display: flex; align-items: center;
    padding-left: 43px; color: var(--white); white-space: nowrap;
  }
  .phone-icon { width: 42px; height: 42px; flex: none; }
  .phone-number { font-size: 42px; font-weight: 700; margin-left: 8px; letter-spacing: -.3px; }
  .bar-divider { width: 2px; height: 36px; background: var(--white); margin: 0 18px 0 20px; }
  .offer { font-size: 23.5px; font-weight: 700; }
  .offer .highlight { color: var(--mint); }
</style>
</head>
<body>
  <div class="billboard">
    <div class="hero">
      <svg class="url-corner" width="960" height="322" viewBox="0 0 960 322">
        <polygon points="572,0 960,0 960,73 604,73" fill="#ffffff"/>
      </svg>
      <h1 class="headline">Worrying<br>about your<br>money? Us too!</h1>
      <svg class="here-flag" width="172" height="200" viewBox="0 0 172 200">
        <polygon points="0,0 172,0 172,164 86,200 0,164" fill="#00402c"/>
        <polygon points="10,146 86,178 162,146 162,156 86,188 10,156" fill="#00a060"/>
      </svg>
      <div class="here-label">HERE</div>
    </div>
    <div class="site-url">keystoneryllc<span class="tld">.example</span></div>
    <div class="services">
      <span>Planning</span><span class="divider">|</span>
      <span>Investments</span><span class="divider">|</span>
      <span>Taxes</span><span class="divider">|</span>
      <span>Insurance</span>
    </div>
    <div class="contact-bar">
      <svg class="phone-icon" viewBox="0 0 42 42" aria-hidden="true">
        <circle cx="21" cy="21" r="20" fill="#ffffff"/>
        <path d="M14 11c1.2-.8 2.4-.4 3 .8l2 3.6c.5 1 .2 2-.6 2.6l-1.6 1.2c1 2.6 2.8 4.6 5.2 5.8l1.3-1.5c.7-.8 1.800-1 2.7-.4l3.4 2.2c1.1.7 1.3 2 .5 3.1l-1.5 2c-1 1.3-2.7 1.7-4.3 1.1C16.6 28.6 11.9 23 10.4 17c-.4-1.7.1-3.4 1.6-4.6z" fill="#003b28"/>
        <path d="M23 12a7 7 0 0 1 7 7M23 8a11 11 0 0 1 11 11" stroke="#003b28" stroke-width="2" fill="none" stroke-linecap="round"/>
      </svg>
      <span class="phone-number">302-418-2907</span>
      <span class="bar-divider"></span>
      <span class="offer">“No worry” for a <span class="highlight">free consultation</span></span>
    </div>
  </div>
</body>
</html>
```